Velvet Harbor Snout Sticks - our own unique product line of cotton swabs

We have something now that we are not too happy with. Looking to create a label for a line of cotton swabs that we have created and designed to clean your nose from mucus and boogers. The logo that i have so far for the packaging is the white background with the black silhouette nose (attached). We need something that can do well in the retail/consumer market. Our website address (even though it is not live yet) should be listed somewhere on the label....
www.VelvetHarborGoods.example ( we sell pillows, but we have other product lines)
We would also like to see a brief description on how to correctly use the nose pick on the back side of the label. The description on how to use should read " insert cotton nose pick into nostril and give it a few counter clock wise twirls or till you feel mucus/debris latch onto the cotton. You may need to repeat the process and use more than one nose pick to achieve desired result."
As well as a warning mentioning : "Never insert plastic end of nose pick into any part of your body. Be careful and use with caution."
Also for you to know, the cotton is made from 100% natural cotton, the cotton head itself is thick and highly absorbent making it a pleasure to use. There are 50 nose picks per pack.
We're fine with keeping it simple and not making the packaging too busy, however we're open to your ideas and designs! I have given you the most important information relevant to the project. If there are any questions or something is not clear enough please kindly message me.

Requirements
Must have
• professional looking
clean looking
not busy
Should not have
• words clumping together making it appear as too much text in one area
too much text clumped together on the design

```html
<!DOCTYPE html>
<html lang="en">
<head>
<meta charset="utf-8">
<title>Velvet Harbor Snout Sticks – Label</title>
<link rel="stylesheet" href="https://fonts.googleapis.com/css2?family=Montserrat:wght@400;500;600;700;800&family=Yellowtail&display=swap">
<style>
  :root {
    --teal: #3fbfb6;
    --slate: #6b7177;
    --slate-soft: #c9cdd0;
    --paper: #ffffff;
    --canvas: #f4f5f5;
    --rule: #8a8f94;
  }
  * { box-sizing: border-box; margin: 0; padding: 0; }
  html, body { width: 1200px; height: 589px; overflow: hidden; }
  body {
    background: var(--canvas);
    font-family: "Montserrat", sans-serif;
    color: var(--slate);
    position: relative;
  }

  /* ---------- Front label ---------- */
  .front-label {
    position: absolute;
    left: 40px; top: 70px;
    width: 600px; height: 450px;
    background: var(--paper);
    border: 1px solid var(--rule);
    overflow: hidden;
  }
  .brand-name {
    position: absolute;
    left: 52px; top: 48px;
    font-size: 50px;
    font-weight: 500;
    color: var(--slate);
    letter-spacing: -0.5px;
    line-height: 1;
  }
  .brand-dot {
    position: absolute;
    left: 400px; top: 60px;
    width: 28px; height: 28px;
    border-radius: 50%;
    background: var(--slate);
  }
  .cotton-badge {
    position: absolute;
    left: 434px; top: 92px;
    width: 104px; height: 104px;
    border-radius: 50%;
    border: 2px solid var(--teal);
    background: #e6f6f5;
  }
  .nose-art {
    position: absolute;
    left: 37px; top: 153px;
    width: 190px; height: 200px;
    background: linear-gradient(160deg, #eef0f1 0%, #d7dbdd 100%);
    border-radius: 6px;
  }
  .claim {
    position: absolute;
    left: 150px; top: 196px;
    font-size: 19px;
    font-weight: 700;
    letter-spacing: 2px;
    color: var(--slate);
  }
  .title-band {
    position: absolute;
    left: 127px; top: 222px;
    width: 473px; height: 73px;
    background: var(--teal);
    color: var(--paper);
  }
  .title-band .product-name {
    position: absolute;
    left: 46px; top: 4px;
    font-size: 47px;
    font-weight: 800;
    letter-spacing: 3px;
    line-height: 1;
  }
  .title-band .tagline {
    position: absolute;
    left: 72px; top: 54px;
    font-size: 11.5px;
    font-weight: 700;
    letter-spacing: 0.3px;
  }
  .question {
    position: absolute;
    left: 217px; top: 303px;
    font-family: "Yellowtail", cursive;
    font-size: 28px;
    color: var(--slate);
    line-height: 1;
  }
  .swab-stick {
    position: absolute;
    left: 226px; top: 341px;
    width: 305px; height: 5px;
    background: var(--slate);
  }
  .count {
    position: absolute;
    right: 75px; top: 352px;
    text-align: center;
    color: var(--slate);
    line-height: 1;
  }
  .count .number { display: block; font-size: 52px; font-weight: 800; }
  .count .unit { display: block; font-size: 20px; font-weight: 700; margin-top: -4px; }
  .website {
    position: absolute;
    left: 52px; top: 400px;
    font-size: 15px;
    font-weight: 600;
    letter-spacing: 1.2px;
    color: var(--teal);
  }

  /* ---------- Back label ---------- */
  .back-label {
    position: absolute;
    left: 660px; top: 179px;
    width: 520px; height: 231px;
    background: var(--paper);
    border: 1px solid var(--rule);
  }
  .step-icon {
    position: absolute;
    left: 36px;
    width: 64px; height: 64px;
    border-radius: 50%;
    border: 3px solid var(--teal);
    background: #e6f6f5;
  }
  .step-icon.one { top: 13px; }
  .step-icon.two { top: 84px; }
  .step-icon.three { top: 153px; }
  .usage-heading {
    position: absolute;
    left: 118px; top: 26px;
    width: 367px;
    display: flex;
    align-items: center;
    gap: 6px;
    font-size: 15px;
    font-weight: 700;
    letter-spacing: 0.5px;
    color: var(--teal);
    white-space: nowrap;
  }
  .usage-heading::before,
  .usage-heading::after {
    content: "";
    flex: 1;
    border-top: 3px dotted var(--teal);
  }
  .usage-text {
    position: absolute;
    left: 118px; top: 53px;
    width: 367px;
    font-size: 12.6px;
    line-height: 20px;
    text-align: justify;
    text-align-last: justify;
    color: var(--slate);
  }
  .usage-text .last-line { text-align-last: left; }
  .warning {
    position: absolute;
    left: 115px; top: 165px;
    width: 370px; height: 40px;
    border-radius: 8px;
    background: var(--teal);
    color: var(--paper);
    font-size: 11.5px;
    font-weight: 500;
    line-height: 16px;
    text-align: center;
    padding-top: 4px;
  }
</style>
</head>
<body>

  <section class="front-label" aria-label="Front label">
    <div class="brand-name">Velvet Harbor</div>
    <div class="brand-dot"></div>
    <div class="cotton-badge" role="img" aria-label="Natural cotton, highly absorbent badge"></div>
    <div class="nose-art" role="img" aria-label="Side profile nose line drawing with cotton swab tip"></div>
    <div class="claim">100% NATURAL COTTON</div>
    <div class="title-band">
      <div class="product-name">SNOUT STICKS</div>
      <div class="tagline">CLEAN YOUR NOSE FROM MUCUS AND BOOGERS</div>
    </div>
    <div class="question">How do you pick your nose?</div>
    <div class="swab-stick"></div>
    <div class="count"><span class="number">50</span><span class="unit">count</span></div>
    <div class="website">www.VelvetHarborGoods.example</div>
  </section>

  <section class="back-label" aria-label="Back label">
    <div class="step-icon one" role="img" aria-label="Step illustration: inserting swab into nostril"></div>
    <div class="step-icon two" role="img" aria-label="Step illustration: twirling swab counter clockwise"></div>
    <div class="step-icon three" role="img" aria-label="Step illustration: removing the used swab"></div>
    <h2 class="usage-heading">HOW TO USE</h2>
    <p class="usage-text">Insert cotton nose pick into nostril and give it a few counter clock wise twirls or till you feel mucus/debris latch onto the cotton. You may need to repeat the process and use more than <span class="last-line">one nose pick to achieve desired result.</span></p>
    <div class="warning">Never insert plastic end of nose pick into any part<br>of your body. Be careful and use with caution.</div>
  </section>

</body>
</html>
```